BRISKLY sparkling water needs new artwork! Based in Southern California

"Briskly" is a new sparkling water company based in Southern California that offers refreshing flavors (lime, cherry, & mango) with B vitamins and antioxidants.

We would like to see packaging designs for standard 12oz cans for each of the three flavors.
Our initial preference is to have individual artwork for each flavor.

Attached are examples of competitors' designs.
Updates

We are extending the deadline for the Thanksgiving Holiday. Thank you all for your contributions.

```html
<!DOCTYPE html>
<html lang="en">
<head>
<meta charset="utf-8">
<title>Briskly Sparkling Water – Lime Can Label</title>
<link href="https://fonts.googleapis.com/css2?family=Kalam:wght@400;700&display=swap" rel="stylesheet">
<style>
  :root {
    --page-bg: #e8e8e8;
    --label-light: #eef25a;
    --label-mid: #d9e02c;
    --label-deep: #c5cc1e;
    --ink: #333333;
    --badge-white: #f7f7f5;
    --ribbon-green: #8cc95a;
    --ribbon-text: #ffffff;
    --flavor-green: #7dbf48;
    --flavor-text: #eef7c8;
    --lime-art: #a9d86a;
    --lineart-tone: #dfe63e;
    --volume-text: #f4f6b0;
  }
  * { margin: 0; padding: 0; box-sizing: border-box; }
  html, body {
    width: 1174px;
    height: 1200px;
    overflow: hidden;
    background: var(--page-bg);
    font-family: "Kalam", cursive;
  }
  .can-label {
    position: absolute;
    left: 227px;
    top: 50px;
    width: 720px;
    height: 1100px;
    background: linear-gradient(90deg, var(--label-deep) 0%, var(--label-light) 45%, var(--label-mid) 100%);
    overflow: hidden;
  }
  .lineart-scatter {
    position: absolute;
    left: 40px;
    top: 40px;
    width: 640px;
    height: 180px;
    border-radius: 30px;
    background: radial-gradient(ellipse at center, var(--lineart-tone) 0%, rgba(223,230,62,0) 70%);
  }
  .brand-name {
    position: absolute;
    left: 0;
    width: 100%;
    top: 210px;
    text-align: center;
    font-weight: 700;
    font-size: 120px;
    line-height: 1;
    color: var(--ink);
  }
  .title-badge {
    position: absolute;
    left: 70px;
    top: 400px;
    width: 580px;
    height: 320px;
  }
  .title-badge svg { position: absolute; inset: 0; }
  .title-text {
    position: absolute;
    inset: 0;
    display: flex;
    flex-direction: column;
    align-items: center;
    justify-content: center;
    color: var(--ink);
    font-weight: 700;
    line-height: 0.95;
    padding-top: 10px;
  }
  .title-text .line-one { font-size: 76px; letter-spacing: 1px; }
  .title-text .line-two { font-size: 112px; letter-spacing: 4px; }
  .benefit-ribbon {
    position: absolute;
    left: 70px;
    top: 712px;
    width: 580px;
    height: 52px;
    background: var(--ribbon-green);
    border-radius: 6px;
    color: var(--ribbon-text);
    font-size: 26px;
    font-weight: 700;
    text-align: center;
    line-height: 52px;
    letter-spacing: 1px;
  }
  .lime-illustration {
    position: absolute;
    left: 30px;
    top: 820px;
    width: 250px;
    height: 230px;
    border-radius: 50%;
    background: radial-gradient(circle at 45% 45%, var(--lime-art) 0%, #96cc55 70%, rgba(150,204,85,0) 72%);
  }
  .flavor-tag {
    position: absolute;
    left: 320px;
    top: 810px;
    width: 310px;
    height: 180px;
  }
  .flavor-tag svg { position: absolute; inset: 0; }
  .flavor-text {
    position: absolute;
    inset: 0;
    display: flex;
    flex-direction: column;
    align-items: center;
    justify-content: center;
    color: var(--flavor-text);
    font-weight: 700;
    line-height: 0.95;
  }
  .flavor-text .flavor-name { font-size: 70px; }
  .flavor-text .flavor-word { font-size: 46px; }
  .volume {
    position: absolute;
    right: 80px;
    top: 1020px;
    font-size: 26px;
    color: var(--volume-text);
    letter-spacing: 1px;
  }
</style>
</head>
<body>
  <main class="can-label">
    <div class="lineart-scatter" role="img" aria-label="Scattered line drawings of limes, leaves and bubbles"></div>

    <h1 class="brand-name">Briskly</h1>

    <section class="title-badge">
      <svg viewBox="0 0 580 320" width="580" height="320" aria-hidden="true">
        <path d="M30 40 C130 10 200 30 290 20 C380 10 450 30 550 40 C575 120 570 200 550 280 C450 300 380 285 290 295 C200 305 130 290 30 280 C10 200 5 120 30 40 Z"
              fill="var(--badge-white)" stroke="var(--ink)" stroke-width="10" stroke-linejoin="round"/>
      </svg>
      <div class="title-text">
        <span class="line-one">SPARKLING</span>
        <span class="line-two">WATER</span>
      </div>
    </section>

    <p class="benefit-ribbon">WITH B VITAMINS AND ANTIOXIDANTS</p>

    <div class="lime-illustration" role="img" aria-label="Illustration of a whole lime with leaves"></div>

    <div class="flavor-tag">
      <svg viewBox="0 0 310 180" width="310" height="180" aria-hidden="true">
        <path d="M30 40 C90 5 230 0 285 25 C310 70 300 130 270 160 C200 180 90 178 25 150 C5 110 8 70 30 40 Z"
              fill="var(--flavor-green)"/>
      </svg>
      <div class="flavor-text">
        <span class="flavor-name">LiME</span>
        <span class="flavor-word">FLAVOR</span>
      </div>
    </div>

    <p class="volume">12oz (355mL)</p>
  </main>
</body>
</html>
```